Tea Shop - Drinks Menu - Vertical TV screen

Need a drinks menu design for a tea shop based in The Netherlands. Called BrewHaven.
Currently we are trying to attract more customers for our Cup4Road and the idea came up to place 3 TV screen vertically in order to use 2 for the menu.
Website: http://brewhaven-dorpsplein.example/
Posible colour themes -
- Light green (same green as logo)
- Light brown
Dimensions of the screen -
- 40inch
- 905 mm Height
- 207 mm Width
Resolution of the menu must be 1920x1080 BUT VERTICAL
Needs to contain the following -
- Hot Cup4Road
- BLACK
- Delicate Velvet Dusk
- Sweet Papaya Hug
- Plummy Orchard
- Spicy Chai
- Black Assam
- Duke of Highbrook
- Smokey Lapsang Suochong
- ( and many more teas, so leave space for aditional 5+)
- GREEN
- Sencha Kiwi-Clove
- Sencha Meadow Cherries
- Sencha Melon Toffee
- Bright Lotus
- Bancha
- Classic Cloudburst
- (space for aditional 4+)
- OOLONG
- Pebble Oolong
- Creamy Oolong
- WHITE
- Bai Mu Tan
- HERBAL
- BrewHaven's Dream
- Refreshing Linden
- Pure Ginger
- Moon Blend
- Lulu Sage
- Thyme Blueberry
- FRUIT TEA
- Zesty Walnut
- Jolly Berry
- Guava Hug
- Zingy Quince
- Sunset Plum
- (space for aditional 2+)
- LATTÉ
- Spiced Chai
- Green Chai
- Vanille Chai
- Matcha
- Fresh Mint tea
- Iced Tea
- Peach
- Raspberry
- Lemon
- Mango
Divide this menu over 2 TV screens with the mentioned dimensions and use the font provided in the uploaded files (not mandatory if you think you have a bette idea).
Simple
Needs to attract people
Easy to adjust
Idea's are always welcome and appreciated
LOGO LINK : http://img42.picvault.example/8qz4rk1.png
(image too big to upload on here, sorry)
people whom drink TEA
Tv

```html
<!DOCTYPE html>
<html lang="en">
<head>
<meta charset="utf-8">
<title>Hot Cup4Road – BrewHaven Tea Menu</title>
<link rel="stylesheet" href="https://fonts.googleapis.com/css2?family=Nunito+Sans:wght@600;700;800;900&display=swap">
<style>
  :root {
    --paper-light: #efd9a4;
    --paper-mid: #e2bf7c;
    --paper-deep: #c98f4f;
    --rust: #6e2e1c;
    --title-brown: #4b3127;
    --heading-orange: #b9652b;
    --ink: #2b2118;
    --band: rgba(255, 246, 222, 0.35);
    --photo-warm: #b07a45;
    --photo-cream: #f1e6d2;
    --photo-dark: #5b3a22;
  }
  * { margin: 0; padding: 0; box-sizing: border-box; }
  html, body { width: 675px; height: 1200px; overflow: hidden; background: #fff; }
  .screen {
    position: relative;
    width: 675px;
    height: 1200px;
    overflow: hidden;
    font-family: "Nunito Sans", "Avenir Next", sans-serif;
    color: var(--ink);
    background:
      radial-gradient(ellipse 70% 40% at 40% 55%, var(--paper-light) 0%, transparent 75%),
      linear-gradient(180deg, #d9a260 0%, var(--paper-mid) 22%, var(--paper-light) 50%, var(--paper-mid) 80%, #d8ad72 100%);
  }
  .hero-photo {
    position: absolute;
    left: 0; top: 0;
    width: 675px; height: 240px;
    background:
      radial-gradient(ellipse 22% 32% at 46% 55%, #7d6a3c 0%, #a78a55 55%, transparent 100%),
      radial-gradient(ellipse 60% 80% at 10% 10%, #a4462b 0%, transparent 70%),
      radial-gradient(ellipse 50% 80% at 95% 20%, #a95a33 0%, transparent 70%),
      linear-gradient(180deg, #c88754 0%, rgba(226, 191, 124, 0) 100%);
  }
  .title {
    position: absolute;
    left: 0; width: 675px;
    top: 238px;
    text-align: center;
    font-size: 89px;
    font-weight: 900;
    letter-spacing: -1px;
    color: var(--title-brown);
    text-shadow: 2px 3px 4px rgba(60, 35, 15, 0.35);
    line-height: 1;
  }
  .band {
    position: absolute;
    left: 40px; width: 635px; height: 47px;
    background: linear-gradient(90deg, transparent 0%, var(--band) 12%, var(--band) 85%, transparent 100%);
  }
  .band--top { top: 372px; }
  .band--bottom { top: 711px; }
  .group { position: absolute; }
  .group-heading {
    font-size: 39px;
    font-weight: 900;
    color: var(--heading-orange);
    line-height: 1;
    letter-spacing: 0.5px;
  }
  .tea-list { list-style: none; position: absolute; }
  .tea-list li {
    position: relative;
    font-size: 30px;
    font-weight: 600;
    line-height: 35px;
    height: 34.6px;
    white-space: nowrap;
    color: var(--ink);
  }
  .tea-list li::before {
    content: "";
    position: absolute;
    left: -26px; top: 12px;
    width: 12px; height: 12px;
    border: 3px solid var(--heading-orange);
    border-radius: 50%;
  }
  .group--black .group-heading { position: absolute; left: 58px; top: 381px; }
  .group--black .tea-list { left: 57px; top: 437px; }
  .group--oolong .group-heading { position: absolute; left: 431px; top: 374px; }
  .group--oolong .tea-list { left: 423px; top: 437px; }
  .group--oolong .tea-list li { height: 39px; }
  .group--green .group-heading { position: absolute; left: 59px; top: 721px; }
  .group--green .tea-list { left: 59px; top: 767px; }
  .group--white .group-heading { position: absolute; left: 453px; top: 721px; }
  .single-tea {
    position: absolute;
    left: 450px; top: 779px;
    font-size: 30px; font-weight: 600; line-height: 35px;
  }
  .cups-photo {
    position: absolute;
    left: 0; top: 925px;
    width: 300px; height: 275px;
    background:
      radial-gradient(ellipse 45% 60% at 55% 40%, var(--photo-cream) 0%, #e4cfa8 55%, transparent 100%),
      linear-gradient(180deg, rgba(176, 122, 69, 0) 0%, var(--photo-warm) 55%, var(--photo-dark) 100%);
  }
  .iced-photo {
    position: absolute;
    left: 300px; top: 840px;
    width: 375px; height: 360px;
    background:
      radial-gradient(ellipse 30% 42% at 50% 62%, #2e1d12 0%, #8a5c36 60%, transparent 100%),
      linear-gradient(180deg, rgba(200, 150, 90, 0) 0%, rgba(150, 130, 120, 0.55) 100%);
  }
</style>
</head>
<body>
  <main class="screen">
    <div class="hero-photo" role="img" aria-label="Photo of a wooden scoop filled with loose leaf tea over a warm ornamental background"></div>

    <h1 class="title">Hot Cup4Road</h1>

    <div class="band band--top"></div>
    <div class="band band--bottom"></div>

    <section class="group group--black">
      <h2 class="group-heading">BLACK</h2>
      <ul class="tea-list">
        <li>Delicate Velvet Dusk</li>
        <li>Sweet Papaya Hug</li>
        <li>Plummy Orchard</li>
        <li>Spicy Chai</li>
        <li>Black Assam</li>
        <li>Duke of Highbrook</li>
        <li>Smokey Lapsang Suochong</li>
      </ul>
    </section>

    <section class="group group--oolong">
      <h2 class="group-heading">OOLONG</h2>
      <ul class="tea-list">
        <li>Pebble Oolong</li>
        <li>Creamy Oolong</li>
      </ul>
    </section>

    <div class="cups-photo" role="img" aria-label="Photo of hot tea takeaway cups with cardboard sleeves"></div>
    <div class="iced-photo" role="img" aria-label="Photo of an iced tea cup with a pink straw and cardboard sleeve"></div>

    <section class="group group--green">
      <h2 class="group-heading">GREEN</h2>
      <ul class="tea-list">
        <li>Sencha Kiwi-Clove</li>
        <li>Sencha Meadow Cherries</li>
        <li>Sencha Melon Toffee</li>
        <li>Bright Lotus</li>
        <li>Bancha</li>
        <li>Classic Cloudburst</li>
      </ul>
    </section>

    <section class="group group--white">
      <h2 class="group-heading">WHITE</h2>
      <p class="single-tea">Bai Mu Tan</p>
    </section>
  </main>
</body>
</html>
```